Medical Skincare services/menu/pricing Booklet 12 pages

We need produce a 12-page glossy, saddle-stitched booklet (5 1/2" tall X 81/2" wide). The booklet will be used as a services menu for a skin care salon. I have mocked up the booklet (w/ all copy) in WORD and I've provided a separate PDF of the accurate page order (see files attached). IMPORTANT: Feel free to use your creativity yet style-wise it should kinda match my wife's website colors and text style. Her clients are demanding so she wants a clean, high end, modern look (ala Apple maybe?). See her website for a frame of reference www.GlowWithMara.com
Updates

Target Market(s)

upscale female, professional women, teens with acne

Industry/Entity Type

Medical

Requirements
Must have
• the pics in the mock up are important. I've attached them here

```html
<!DOCTYPE html>
<html lang="en">
<head>
<meta charset="utf-8">
<title>Testimonials</title>
<link href="https://fonts.googleapis.com/css2?family=Roboto+Condensed:wght@500&family=Open+Sans:wght@400;700&family=Roboto:wght@300&display=swap" rel="stylesheet">
<style>
  :root {
    --ink: #000000;
    --paper: #ffffff;
    --title-grey: #a6a6a6;
    --label: #1a1a1a;
  }
  * { margin: 0; padding: 0; box-sizing: border-box; }
  html, body { width: 1200px; height: 777px; overflow: hidden; background: var(--paper); }
  .page { position: relative; width: 1200px; height: 777px; background: var(--paper); }
  .bubbles { position: absolute; inset: 0; }
  .bubbles path, .bubbles circle { fill: var(--ink); }

  .page-title {
    position: absolute; left: 20px; top: 36px; height: 708px; width: 100px;
    writing-mode: vertical-rl; transform: rotate(180deg);
    font-family: "Roboto", Arial, sans-serif; font-weight: 300;
    font-size: 101px; line-height: 100px; color: var(--title-grey);
    text-align: center; letter-spacing: 1px;
  }

  .quote {
    position: absolute; transform: translateX(-50%);
    font-family: "Roboto Condensed", "Arial Narrow", sans-serif; font-weight: 500;
    color: var(--paper); text-align: center; white-space: nowrap;
  }
  .quote--tessa  { left: 316px; top: 54px;  font-size: 22px; line-height: 28px; }
  .quote--carla  { left: 614px; top: 48px;  font-size: 23px; line-height: 31.7px; }
  .quote--melody { left: 976px; top: 73px;  font-size: 23px; line-height: 33.3px; }
  .quote--kendra { left: 396px; top: 353px; font-size: 23px; line-height: 25.8px; }
  .quote--elena  { left: 826px; top: 388px; font-size: 21.5px; line-height: 23.7px; letter-spacing: -0.3px; }

  .client {
    position: absolute; font-family: "Open Sans", Arial, sans-serif;
    color: var(--label); font-size: 15px; line-height: 19px;
  }
  .client__name { display: block; font-weight: 700; font-size: 18px; line-height: 22px; color: var(--ink); }
  .client--tessa  { left: 132px; top: 298px; text-align: left; }
  .client--carla  { right: 530px; top: 370px; text-align: right; }
  .client--kendra { right: 888px; top: 656px; text-align: right; }
  .client--elena  { right: 484px; top: 664px; text-align: right; }
  .client--melody { right: 26px;  top: 552px; text-align: right; }
</style>
</head>
<body>
<main class="page">
  <h1 class="page-title">TESTIMONIALS</h1>

  <svg class="bubbles" width="1200" height="777" viewBox="0 0 1200 777" aria-hidden="true">
    <circle cx="316" cy="160" r="132"/>
    <path d="M384,272 Q350,360 240,390 Q300,340 300,280 Z"/>
    <circle cx="614" cy="200" r="166"/>
    <path d="M752,280 Q740,430 618,494 Q690,420 690,340 Z"/>
    <circle cx="976" cy="216" r="182"/>
    <path d="M1125,326 Q1110,472 1032,546 Q1078,450 1040,388 Z"/>
    <circle cx="396" cy="510" r="156"/>
    <path d="M440,650 Q400,720 250,740 Q340,700 350,660 Z"/>
    <circle cx="826" cy="522" r="164"/>
    <path d="M880,672 Q790,744 616,730 Q720,726 784,676 Z"/>
  </svg>

  <p class="quote quote--tessa">Mara is<br>someone<br>I definitely trust with<br>my skincare needs<br>because she truly cares<br>about people and<br>their issues.</p>

  <p class="quote quote--carla">I<br>have been seeing<br>Mara Ellison for<br>HydroGlow facials. Ever since my<br>first HydroGlow facial my skin has<br>had a healthy glow and texture.<br>As an Aesthetic Professional,<br>she helps me feel my<br>personal best.</p>

  <p class="quote quote--melody">Having ethnic skin<br>I’ve been hesitant about<br>having treatments but Mara<br>immediately put me at ease. She<br>has taught me so much about my<br>skin and how to care for it. Each<br>time I’ve left with my skin<br>looking and feeling<br>amazing</p>

  <p class="quote quote--kendra">I<br>have now had<br>two facials by Mara and<br>each time my skin feels so<br>refreshed and new! She has<br>also helped my teenage son<br>who has acne. Mara knew<br>exactly what he needed and<br>is already getting clearer<br>skin. Worth every<br>penny</p>

  <p class="quote quote--elena">I’ve<br>been seeing Mara<br>on a regular basis<br>because she always goes<br>above and beyond to ensure<br>that I’m comfortable. She<br>made the experience all about<br>me and my skincare needs.<br>She is highly knowledgable<br>and offers creative options<br>to make sure I get<br>what I need.</p>

  <p class="client client--tessa"><span class="client__name">Tessa Lowell</span>Realty TV Star<br>/Coastal Lives of<br>Laguna County</p>
  <p class="client client--carla"><span class="client__name">CARLA MINTON,</span>R.N.</p>
  <p class="client client--kendra"><span class="client__name">KENDRA MILES</span>- Mother of Five</p>
  <p class="client client--elena"><span class="client__name">ELENA STRAND</span>- Marketing Exec.</p>
  <p class="client client--melody"><span class="client__name">MELODY HARPER</span>- Real Estate Agent</p>
</main>
</body>
</html>
```